Harrow Grading LLC business card design

Excavation company business cards

Contact Information for Business Card

Harrow Grading LLC cell phone 208-417-6290 office phone 208-319-4856 harrowgradingllc@maplecove.com Driveways, site prep, retaining walls, septic systems, rock delivery

Colors

Designer to choose colors to be used in the design.

```html
<!DOCTYPE html>
<html lang="en">
<head>
<meta charset="utf-8">
<title>Harrow Grading LLC – Business Card</title>
<link href="https://fonts.googleapis.com/css2?family=Montserrat:wght@400;500;700;800&display=swap" rel="stylesheet">
<style>
  :root {
    --orange: #ee6f22;
    --ink: #1c1c1c;
    --grey: #5a5a5a;
    --paper: #ffffff;
    --backdrop: #e6e4e1;
  }
  * { margin: 0; padding: 0; box-sizing: border-box; }
  html, body { width: 1200px; height: 912px; overflow: hidden; }
  body {
    background: var(--backdrop);
    font-family: "Montserrat", sans-serif;
    position: relative;
  }
  .card {
    position: absolute;
    left: 250px;
    width: 700px;
    height: 400px;
    box-shadow: 0 6px 18px rgba(0,0,0,.18);
    overflow: hidden;
  }
  /* Front */
  .card-front { top: 36px; background: var(--ink); }
  .front-art {
    position: absolute;
    left: 250px; top: 70px;
    width: 200px; height: 130px;
    border-radius: 6px;
    background: linear-gradient(160deg, #4a3a30 0%, #9a4f22 100%);
  }
  .front-name {
    position: absolute;
    left: 0; right: 0; top: 226px;
    text-align: center;
    color: var(--orange);
    font-weight: 800;
    font-size: 46px;
    letter-spacing: .5px;
  }
  /* Back */
  .card-back { top: 476px; background: var(--paper); }
  .holder {
    position: absolute;
    right: 44px; top: 34px;
    text-align right;
    text-align: right;
  }
  .holder-name { color: var(--orange); font-weight: 800; font-size: 24px; letter-spacing: .3px; }
  .holder-title { color: var(--grey); font-size: 17px; margin-top: 2px; }
  .holder-tab {
    position: absolute;
    right: 0; top: 34px;
    width: 18px; height: 30px;
    background: var(--orange);
  }
  .back-name {
    position: absolute;
    left: 40px; top: 40px;
    color: var(--orange);
    font-weight: 800;
    font-size: 30px;
  }
  .contacts {
    position: absolute;
    left: 40px; top: 118px;
    list-style: none;
    color: var(--grey);
    font-size: 19px;
    line-height: 27px;
  }
  .contacts li { display: flex; align-items: center; gap: 8px; }
  .contacts svg { width: 14px; height: 14px; flex: none; }
  .services {
    position: absolute;
    left: 40px; top: 212px;
  }
  .services-title { color: var(--orange); font-weight: 700; font-size: 20px; margin-bottom: 2px; }
  .services ul { list-style: none; color: var(--grey); font-size: 19px; line-height: 25px; }
  .services li::before { content: "•"; color: var(--orange); margin-right: 6px; }
  .back-art {
    position: absolute;
    right: 0; bottom: 0;
    width: 260px; height: 190px;
    background: linear-gradient(150deg, #d8d8d8 0%, #f2b48c 100%);
  }
</style>
</head>
<body>
  <section class="card card-front">
    <div class="front-art" role="img" aria-label="Illustration of an excavator in front of mountain peaks"></div>
    <div class="front-name">Harrow Grading LLC</div>
  </section>

  <section class="card card-back">
    <div class="back-name">Harrow Grading LLC</div>

    <div class="holder">
      <div class="holder-name">DALE MORROW</div>
      <div class="holder-title">Director</div>
    </div>
    <div class="holder-tab"></div>

    <ul class="contacts">
      <li>
        <svg viewBox="0 0 14 14"><rect x="3.5" y="1" width="7" height="12" rx="1.5" fill="none" stroke="#ee6f22" stroke-width="1.5"/></svg>
        208-417-6290
      </li>
      <li>
        <svg viewBox="0 0 14 14"><path d="M2 6c0-3 10-3 10 0v1H9V5.5H5V7H2z M3 8h8l1 5H2z" fill="#ee6f22"/></svg>
        208-319-4856
      </li>
      <li>
        <svg viewBox="0 0 14 14"><rect x="1" y="3" width="12" height="8" fill="none" stroke="#ee6f22" stroke-width="1.4"/><path d="M1 3l6 5 6-5" fill="none" stroke="#ee6f22" stroke-width="1.4"/></svg>
        harrowgradingllc@maplecove.com
      </li>
    </ul>

    <div class="services">
      <div class="services-title">Harrow Grading LLC</div>
      <ul>
        <li>Driveways,</li>
        <li>site prep,</li>
        <li>retaining walls,</li>
        <li>septic systems,</li>
        <li>rock delivery</li>
      </ul>
    </div>

    <div class="back-art" role="img" aria-label="Illustration of an excavator with a mountain outline"></div>
  </section>
</body>
</html>
```